Heron Dusk business card design

I make handmade colourful women's beaded jewellery (necklaces and earnings).
I require a business card to be designed to truly reflect my jewellery, that is, it is different and stands out.
I would like the business card to look creative, arty, gentle and feminine and fit in with the look of my website and logo (already developed).
I would like the business card to have strong use of the water reeds that are flowing in the wind (please see the banner image on my website www.herondusk.net and attached files).

Target Market(s)

Women who are fashion conscious, hip and funky. My audience like things that are a little different and stand out in a crowd.These women are aged in their 20's-40's.

Industry/Entity Type

Jewelry

Contact Information for Business Card

Please include the following items:
1) my logo: Heron Dusk
2) my name, address and phone number: Darla Fontenot, Sydney, Australia, 0498 315 270
3) my web details: www.herondusk.net, info@herondusk.net, www.facebook.com/herondusk

Font styles to use
Other font styles liked:
• Remachine Script

Requirements
Must have
• My business card must have the following:
• 1) my personal details including all my website contacts (see above).
• 2) Heron Dusk logo
• 3) Reeds flowing in the wind (see my banner image on my website www.herondusk.net or see attached files).
Nice to have
• A sunrise in the background (rising over water)
• I would prefer that the colour scheme to fit with the Heron Dusk logo, that is the colours of an early morning sunrise i.e yellows, oranges. The use of black and white is fine.
Should not have
• I do not like a commercial manufactured look with hard edges. I would like a look that is soft and reflects an artistic, creative and independent business.

```html
<!DOCTYPE html>
<html lang="en">
<head>
<meta charset="utf-8">
<title>Heron Dusk – Business Cards</title>
<link rel="stylesheet" href="https://fonts.googleapis.com/css2?family=Arimo:wght@400;700&display=swap">
<style>
  :root {
    --backdrop: #2b2b2b;
    --card: #ffffff;
    --card-back: #f4f4f4;
    --ink: #1e1e1e;
    --ink-soft: #6a6a6a;
    --sun: #f7b500;
    --sun-deep: #ee8a00;
    --sun-light: #ffd84a;
    --reed: #cfcfcf;
    --divider: #dedede;
  }
  * { box-sizing: border-box; margin: 0; padding: 0; }
  html, body { width: 1200px; height: 950px; overflow: hidden; }
  body {
    background: var(--backdrop);
    font-family: "Arimo", Arial, sans-serif;
    color: var(--ink);
    position: relative;
  }
  .card {
    position: absolute;
    width: 620px;
    height: 354px;
    border-radius: 4px;
    overflow: hidden;
    box-shadow: 0 14px 30px rgba(0,0,0,.45);
  }

  /* Shared brand block: name above a plain sun disc */
  .brand {
    position: absolute;
    display: flex; flex-direction: column; align-items: center; gap: 8px;
  }
  .brand__name {
    font-weight: 700; color: var(--ink);
    white-space: nowrap; line-height: 1.1;
  }
  .brand__mark {
    border-radius: 50%;
    background: radial-gradient(circle at 50% 40%, var(--sun-light), var(--sun) 55%, var(--sun-deep));
    border: 3px solid var(--ink);
    flex: none;
  }

  /* Back side */
  .card--back { left: 70px; top: 60px; background: var(--card-back); }
  .card__reeds {
    position: absolute; inset: 0;
    background:
      linear-gradient(180deg, rgba(244,244,244,1) 0%, rgba(244,244,244,.2) 35%, rgba(200,200,200,.55) 100%),
      linear-gradient(90deg, var(--reed) 0%, #e9e9e9 45%, var(--reed) 100%);
  }
  .card--back .brand { left: 150px; top: 70px; width: 240px; }
  .card--back .brand__name { font-size: 28px; }
  .card--back .brand__mark { width: 118px; height: 118px; }
  .social {
    position: absolute; left: 218px; top: 278px;
    display: flex; gap: 8px; list-style: none;
  }
  .social__dot {
    width: 20px; height: 20px; border-radius: 50%;
    background: var(--sun-deep);
  }
  .social__dot:nth-child(2) { background: var(--sun); }
  .social__dot:nth-child(3) { background: var(--ink-soft); }
  .social__dot:nth-child(4) { background: var(--ink); }

  /* Front side */
  .card--front { left: 510px; top: 520px; background: var(--card); }
  .card--front .brand { left: 20px; top: 44px; width: 260px; }
  .card--front .brand__name { font-size: 26px; }
  .card--front .brand__mark { width: 130px; height: 130px; }
  .divider {
    position: absolute; left: 300px; top: 34px;
    width: 1px; height: 170px; background: var(--divider);
  }
  .contact { position: absolute; left: 322px; top: 36px; }
  .contact__name { font-size: 21px; font-weight: 700; }
  .contact__role { font-size: 14px; color: var(--sun); margin-top: 2px; }
  .contact__lines { list-style: none; margin-top: 14px; font-size: 14px; color: var(--ink-soft); line-height: 21px; }
  .contact__lines li { display: flex; align-items: center; gap: 8px; }
  .contact__icon { width: 14px; height: 14px; flex: none; fill: var(--ink); }
  .swoosh { position: absolute; left: 0; bottom: 0; width: 620px; height: 130px; }
  .swoosh__url {
    font-family: "Arimo", Arial, sans-serif;
    font-size: 15px; font-weight: 700; letter-spacing: 3px; fill: var(--ink);
  }
</style>
</head>
<body>

  <section class="card card--back" aria-label="Business card, back">
    <div class="card__reeds" role="img" aria-label="Grey water reeds and bulrushes swaying in the wind"></div>
    <div class="brand">
      <span class="brand__name">Heron Dusk</span>
      <span class="brand__mark"></span>
    </div>
    <ul class="social" aria-label="Social links">
      <li class="social__dot"></li>
      <li class="social__dot"></li>
      <li class="social__dot"></li>
      <li class="social__dot"></li>
    </ul>
  </section>

  <section class="card card--front" aria-label="Business card, front">
    <div class="brand">
      <span class="brand__name">Heron Dusk</span>
      <span class="brand__mark"></span>
    </div>
    <span class="divider"></span>
    <div class="contact">
      <p class="contact__name">Mara Quill</p>
      <p class="contact__role">President</p>
      <ul class="contact__lines">
        <li>Darla Fontenot</li>
        <li>Sydney, Australia</li>
        <li>
          <svg class="contact__icon" viewBox="0 0 16 16" aria-hidden="true"><path d="M3.5 1.5l2.5 3-1.5 1.8c.9 1.9 2.3 3.3 4.2 4.2L10.5 9l3 2.5-1.5 2.8C6.5 14 2 9.5 1 3.5z"/></svg>
          0498 315 270
        </li>
        <li>
          <svg class="contact__icon" viewBox="0 0 16 16" aria-hidden="true"><path d="M1 3h14v10H1z M2 4.2v.5l6 4 6-4v-.5z" fill-rule="evenodd"/></svg>
          info@herondusk.net
        </li>
        <li>
          <svg class="contact__icon" viewBox="0 0 16 16" aria-hidden="true"><rect x="1" y="1" width="14" height="14" rx="2"/></svg>
          herondusk
        </li>
      </ul>
    </div>
    <svg class="swoosh" viewBox="0 0 620 130" aria-label="www.herondusk.net">
      <defs>
        <linearGradient id="sunBand" x1="0" y1="0" x2="1" y2="0">
          <stop offset="0" stop-color="#ffd84a"/>
          <stop offset="1" stop-color="#f4a300"/>
        </linearGradient>
        <path id="urlPath" d="M150 118 C 320 100, 480 70, 620 20"/>
      </defs>
      <path d="M0 120 C 250 115, 470 70, 620 10 L620 130 L0 130 Z" fill="url(#sunBand)"/>
      <path d="M0 108 C 250 104, 470 60, 620 0" fill="none" stroke="#1e1e1e" stroke-width="3"/>
      <path d="M0 110 C 250 106, 470 62, 620 2 L620 130 L0 130 Z" fill="url(#sunBand)"/>
      <text class="swoosh__url"><textPath href="#urlPath" startOffset="30%">www.herondusk.net</textPath></text>
    </svg>
  </section>

</body>
</html>
```